Business Card for my New Brokerage

Looking to get a business card design for my new Real Estate Brokerage.
I want it with Picture, Phone Number, Email, Website, Office Address
Name and Designation. Please add logo too.

Target Market(s)

Real Estate Investors or Home Buyers

Industry/Entity Type

Real Estate

Contact Information for Business Card

Name, Email, Phone Number, website, email, office address

Colors
EB3D1F
EC4F4E
F09395
F8D3D4
FCEDEE

Requirements
Must have
• Minimalistic, Clean, Modern, Photo
Nice to have
• White and Red Colors

```html
<!DOCTYPE html>
<html lang="en">
<head>
<meta charset="UTF-8">
<title>Halvern Realty Inc — Business Card</title>
<link href="https://fonts.googleapis.com/css2?family=Montserrat:wght@400;600;700&display=swap" rel="stylesheet">
<style>
  :root {
    --page-bg: #fdfdfd;
    --card-bg: #f5f5f5;
    --brand-red: #dc0b18;
    --text-grey: #555555;
    --photo-light: #d6d6d8;
    --photo-dark: #b9b9bd;
  }
  * { margin: 0; padding: 0; box-sizing: border-box; }
  html, body {
    width: 1200px; height: 1200px; overflow: hidden;
    background: var(--page-bg);
    font-family: 'Montserrat', sans-serif;
  }
  .canvas { position: relative; width: 1200px; height: 1200px; }
  .card {
    position: absolute; top: 304px;
    width: 336px; height: 571px;
    background: var(--card-bg);
    overflow: hidden;
  }
  .card-front { left: 232px; }
  .card-back { left: 640px; }

  .accent-bands {
    position: absolute; left: 0; top: 0;
    width: 336px; height: 571px;
  }
  .accent-bands polygon { fill: var(--brand-red); }

  .wordmark {
    position: absolute; left: 0; right: 0;
    text-align: center; color: var(--brand-red);
    font-weight: 600; line-height: 1;
  }
  .wordmark .name { display: block; }
  .wordmark .sub { display: block; font-weight: 500; }

  .card-front .wordmark { top: 152px; }
  .card-front .wordmark .name { font-size: 50px; letter-spacing: 1px; }
  .card-front .wordmark .sub { font-size: 19px; letter-spacing: 5px; margin-top: 8px; }

  .portrait {
    position: absolute; left: 88px; top: 58px;
    width: 248px; height: 165px;
    background: linear-gradient(135deg, var(--photo-light), var(--photo-dark));
    clip-path: polygon(72px 0, 248px 0, 248px 165px, 73px 165px, 0 73px);
  }

  .contact {
    position: absolute; left: 0; right: 0; top: 281px;
    text-align: center; color: var(--text-grey);
    font-size: 15px; line-height: 19.5px; font-weight: 400;
  }
  .contact .agent-name { font-weight: 700; font-size: 15px; letter-spacing: 0.3px; }
  .contact .group { margin-bottom: 19px; }

  .card-back .wordmark { top: 508px; }
  .card-back .wordmark .name { font-size: 28px; letter-spacing: 0.5px; }
  .card-back .wordmark .sub { font-size: 10px; letter-spacing: 3px; margin-top: 4px; }
</style>
</head>
<body>
<div class="canvas">
  <section class="card card-front">
    <svg class="accent-bands" viewBox="0 0 336 571" aria-hidden="true">
      <polygon points="197,286 276,286 0,568 0,488"/>
      <polygon points="336,392 336,436 201,571 157,571"/>
    </svg>
    <div class="wordmark">
      <span class="name">HALVERN</span>
      <span class="sub">REALTY INC</span>
    </div>
  </section>

  <section class="card card-back">
    <svg class="accent-bands" viewBox="0 0 336 571" aria-hidden="true">
      <polygon points="114,0 160,0 0,164 0,116"/>
    </svg>
    <div class="portrait" role="img" aria-label="Portrait photo of the agent"></div>
    <div class="contact">
      <div class="group">
        <div class="agent-name">DANIEL MERCER</div>
        <div>daniel@halvern.com</div>
        <div>123 456 789 0</div>
      </div>
      <div class="group">
        <div>www.halvern.com</div>
        <div>info@halvern.com</div>
      </div>
      <div class="group">
        <div>Street xxxx, 123</div>
        <div>456 xxx xxxxxx</div>
      </div>
    </div>
    <div class="wordmark">
      <span class="name">HALVERN</span>
      <span class="sub">REALTY INC</span>
    </div>
  </section>
</div>
</body>
</html>
```